Tree Service Billboard 20x8 ft

We need a billboard design for a tree service company.
The billboard is 20ft x 8 ft so we need a design that is capable to stretching to those dimensions without loosing quality.
I have attached a series of images.
Image 1- Simply a billboard that I think looks good that I would like you to use for inspiration. I am aiming for the same format only no color in the wording, just black white, or gray. I like the the trees in the background, the logo placed to the left, and wording on the right.
Image 2- Current Logo I would like to the left of the billboard
Image 3- Another format of current logo if needed.
Image 4- A drawn out design template
Image 5- Another drawn out design template

Specific things I am looking for
-The contact number to be the largest thing on the design
-The logo on the design
-Key points to the design to say:
Tree Removal
Tree Trimming
Land Development
Stump Grinding
Storm Response
Insured
Free Bids
-The facebook logo
-The Google Logo

```html
<!DOCTYPE html>
<html lang="en">
<head>
<meta charset="utf-8">
<title>Tree Service Billboard</title>
<link href="https://fonts.googleapis.com/css2?family=Montserrat:wght@800;900&display=swap" rel="stylesheet">
<style>
  :root {
    --canvas: #e9eaec;
    --ink: #0b0b0b;
    --white: #ffffff;
    --green: #1f9a45;
    --grey: #6a6a6a;
    --forest-dark: #1c1c1c;
    --forest-mid: #5a5a5a;
    --forest-light: #8c8c8c;
  }
  html, body {
    margin: 0;
    width: 1200px;
    height: 740px;
    overflow: hidden;
    background: var(--canvas);
  }
  .billboard {
    position: absolute;
    left: 20px;
    top: 90px;
    width: 1160px;
    height: 560px;
    overflow: hidden;
    background: var(--ink);
    font-family: "Montserrat", sans-serif;
    color: var(--white);
  }
  .billboard__art {
    position: absolute;
    inset: 0;
  }
  .services {
    position: absolute;
    left: 56px;
    top: 34px;
    margin: 0;
    padding: 0;
    list-style: none;
    font-weight: 900;
    font-size: 47px;
    line-height: 55px;
    letter-spacing: 0.2px;
    text-shadow: 2px 3px 4px rgba(0,0,0,0.6);
  }
  .brand {
    position: absolute;
    left: 730px;
    top: 36px;
    width: 280px;
    height: 296px;
    display: flex;
    align-items: center;
    justify-content: center;
    text-align: center;
    font-weight: 900;
    font-size: 36px;
    line-height: 42px;
    color: var(--white);
  }
  .contact {
    position: absolute;
    right: 56px;
    bottom: 24px;
    text-align: right;
  }
  .contact__find {
    display: flex;
    align-items: center;
    justify-content: flex-end;
    gap: 14px;
    font-weight: 900;
    font-size: 34px;
    margin-right: 10px;
  }
  .contact__dot {
    width: 40px;
    height: 40px;
    border-radius: 50%;
    background: var(--green);
  }
  .contact__phone {
    display: flex;
    align-items: center;
    gap: 12px;
    font-weight: 900;
    font-size: 92px;
    line-height: 104px;
    letter-spacing: 1px;
  }
  .contact__icon {
    width: 52px;
    height: 52px;
  }
</style>
</head>
<body>
  <div class="billboard">
    <svg class="billboard__art" viewBox="0 0 1160 560" preserveAspectRatio="none">
      <defs>
        <linearGradient id="forestTone" x1="0" y1="0" x2="1" y2="1">
          <stop offset="0" stop-color="var(--forest-mid)"/>
          <stop offset="0.45" stop-color="var(--forest-dark)"/>
          <stop offset="0.75" stop-color="var(--forest-light)"/>
          <stop offset="1" stop-color="var(--forest-mid)"/>
        </linearGradient>
      </defs>
      <rect class="forest-photo" role="img" aria-label="Black and white photo of a dense forest canopy" x="0" y="0" width="1160" height="560" fill="url(#forestTone)"/>
      <path class="swoosh-grey" d="M0,300 C10,400 110,460 320,480 C160,490 40,480 0,470 Z" fill="var(--grey)"/>
      <path class="swoosh-green" d="M740,360 C880,270 1040,250 1160,275 L1160,400 C1080,330 930,320 740,360 Z" fill="var(--green)"/>
      <path class="band-edge" d="M0,455 C220,510 480,500 680,405 C830,335 1000,320 1160,335" fill="none" stroke="var(--white)" stroke-width="5"/>
      <path class="band-black" d="M0,462 C220,517 480,507 684,412 C834,342 1000,328 1160,342 L1160,560 L0,560 Z" fill="var(--ink)"/>
      <circle class="brand-ring" cx="870" cy="184" r="150" fill="none" stroke="var(--white)" stroke-width="9"/>
    </svg>

    <ul class="services">
      <li>TREE REMOVAL</li>
      <li>TREE TRIMMING</li>
      <li>LAND DEVELOPMENT</li>
      <li>STUMP GRINDING</li>
      <li>STORM RESPONSE</li>
      <li>INSURED</li>
      <li>FREE BIDS</li>
    </ul>

    <div class="brand">OAKLINE<br>TREE CO.</div>

    <div class="contact">
      <div class="contact__find">
        <span>FIND US ON</span>
        <span class="contact__dot"></span>
        <span class="contact__dot"></span>
      </div>
      <div class="contact__phone">
        <svg class="contact__icon" viewBox="0 0 24 24" aria-hidden="true">
          <path d="M6.6 10.8a15.1 15.1 0 0 0 6.6 6.6l2.2-2.2a1 1 0 0 1 1-.25 11.4 11.4 0 0 0 3.6.57 1 1 0 0 1 1 1V20a1 1 0 0 1-1 1A17 17 0 0 1 3 4a1 1 0 0 1 1-1h3.5a1 1 0 0 1 1 1c0 1.25.2 2.45.57 3.57a1 1 0 0 1-.25 1z" fill="var(--green)"/>
        </svg>
        <span>555-010-4477</span>
      </div>
    </div>
  </div>
</body>
</html>
```